Business Card Design For Financial Company

Create a new design for company's business card. The corporate logo is attached in several formats. Our new website design is also attached and we would like the business cards to reflect this.
Card needs to contain the following info:
Name
Job Title
Legal company name - eg Varo-Q Capital (Asia) Ltd
Address - eg 612-09 Belmore Plaza,47 Tamsin Street, Hong Kong
Direct tel
Main tel
Fax
Email
Website URL
MS word format preferred. Other formats that can be edited on standard PC also OK.
Updates
Please note the the "VARO-Q" logo nameĀ font is "Gill Sans MT" on Windows
Target Market(s)
Instituation Investors
Industry/Entity Type
Business
Look and feel

```html
<!DOCTYPE html>
<html lang="en">
<head>
<meta charset="utf-8">
<title>Varo-Q Capital – Business Card</title>
<link rel="stylesheet" href="https://fonts.googleapis.com/css2?family=Cabin:wght@400;500&display=swap">
<style>
  :root {
    --backdrop: #97a1a8;
    --card: #ffffff;
    --brand-red: #d7141f;
    --placeholder: #d6d9dc;
    --ink: #1b1b1b;
    --ink-soft: #333333;
    --on-red: #ffffff;
    --shadow: rgba(0, 0, 0, 0.55);
  }
  * { box-sizing: border-box; margin: 0; padding: 0; }
  html, body {
    width: 1200px;
    height: 900px;
    overflow: hidden;
  }
  body {
    position: relative;
    background: var(--backdrop);
    font-family: "Cabin", "Gill Sans MT", "Gill Sans", sans-serif;
    color: var(--ink);
  }
  .card {
    position: absolute;
    background: var(--card);
    box-shadow: 5px 5px 3px var(--shadow);
  }
  .card--front { left: 334px; top: 60px; width: 604px; height: 368px; }
  .card--back  { left: 336px; top: 460px; width: 602px; height: 366px; }

  .tagline-band {
    position: absolute;
    left: 0; top: 202px;
    width: 303px; height: 66px;
    background: var(--brand-red);
    color: var(--on-red);
    font-size: 20px;
    line-height: 26px;
    padding: 7px 0 0 38px;
    letter-spacing: 0.5px;
    white-space: nowrap;
  }
  .brand-mark {
    position: absolute;
    left: 356px; top: 204px;
    display: flex; align-items: center; gap: 17px;
  }
  .brand-mark__placeholder {
    width: 54px; height: 54px;
    background: var(--placeholder);
  }
  .brand-mark__name {
    font-size: 37px;
    font-weight: 400;
    letter-spacing: 1px;
    color: var(--ink);
    white-space: nowrap;
  }

  .holder { position: absolute; left: 39px; top: 33px; font-size: 19px; line-height: 26px; letter-spacing: 0.3px; }
  .holder__name { color: var(--ink); font-weight: 500; }
  .holder__title { color: var(--ink-soft); }

  .brand-band {
    position: absolute;
    right: 0; top: 38px;
    width: 157px; height: 46px;
    background: var(--brand-red);
    color: var(--on-red);
    font-size: 27px;
    line-height: 46px;
    padding-left: 12px;
    letter-spacing: 0.5px;
    white-space: nowrap;
  }

  .company {
    position: absolute; left: 39px; top: 174px;
    font-size: 20px; line-height: 26px; letter-spacing: 0.6px;
    color: var(--ink-soft); font-style: normal; white-space: nowrap;
  }
  .contacts {
    position: absolute; left: 39px; top: 253px; width: 540px;
    font-size: 20px; line-height: 25.5px; letter-spacing: 0.4px;
    color: var(--ink-soft); white-space: nowrap;
  }
  .contacts ul { list-style: none; position: absolute; top: 0; }
  .contacts__phones { left: 0; }
  .contacts__web { left: 243px; }
</style>
</head>
<body>
  <section class="card card--front" aria-label="Card front">
    <div class="tagline-band">INDEPENDENT RESEARCH<br>MARKETING &amp; EXECUTION</div>
    <div class="brand-mark">
      <span class="brand-mark__placeholder"></span>
      <span class="brand-mark__name">VARO-Q</span>
    </div>
  </section>

  <section class="card card--back" aria-label="Card back">
    <div class="holder">
      <p class="holder__name">Daniel Hartley</p>
      <p class="holder__title">Sales Manager</p>
    </div>
    <div class="brand-band">VARO-Q</div>
    <address class="company">
      <p>Varo-Q Capital (Asia) Ltd</p>
      <p>612-09 Belmore Plaza, 47 Tamsin Street, Hong Kong</p>
    </address>
    <div class="contacts">
      <ul class="contacts__phones">
        <li>main tel: 318 205 4470</li>
        <li>direct tel: 447 902 3165</li>
        <li>fax: 021 563 8740</li>
      </ul>
      <ul class="contacts__web">
        <li>contact@varoqcapital.com</li>
        <li>www.varoqcapital.com</li>
      </ul>
    </div>
  </section>
</body>
</html>
```